New Dental Office Needs an Attractive and user friendly Website Designed

I need a website for a new dental office. The Name is Harrowfield Dentistry. I would like a Modern design with a user friendly interface and usability.
I would like a landing page, a page that lists the services we offer: Cosmetic Dentistry, Implants, Dental Hygiene, Emergency Services, Restorations, Dentures
Target Market(s)
Mid to upper class
Industry/Entity Type
Dentistry
Coding
Number of Pages Required
1 page
Requirements
Must have
- Landing page that has a scheduling option, Procedures, operating hours, and contact us info
Nice to have
- Appealing design, Soft comforting colors. Easy to navigate page, Modern and professional.

```html
<!DOCTYPE html>
<html lang="en">
<head>
<meta charset="UTF-8">
<title>Harrowfield Dentistry</title>
<link rel="stylesheet" href="https://fonts.googleapis.com/css2?family=Poppins:wght@400;500;700&family=Playfair+Display:wght@500;600&family=Lato:wght@400;700&display=swap">
<style>
:root{
  --teal:#3fc4b4;
  --teal-soft:#5fbfb2;
  --card-teal:#e2f1ef;
  --sky:#37b9e6;
  --navy:#2d3e50;
  --ink:#111;
  --muted:#6b7280;
  --light:#f5f6f8;
  --gold:#e2b53c;
  --footer:#232323;
  --white:#fff;
}
*{box-sizing:border-box;margin:0;padding:0}
html,body{width:1200px;height:3450px;overflow:hidden}
body{position:relative;background:var(--white);font-family:'Lato',sans-serif;color:var(--ink)}
.abs{position:absolute}

/* hero */
.hero-photo{left:680px;top:0;width:520px;height:576px;border-bottom-left-radius:200px;background:linear-gradient(160deg,#4cc6ee 0%,#2aaee0 60%,#7fb6d6 100%)}
.nav{left:141px;top:35px;width:917px;height:72px;background:var(--white);border-radius:4px;box-shadow:0 2px 12px rgba(0,0,0,.12)}
.brand{position:absolute;left:16px;top:20px;font-family:'Playfair Display',serif;font-weight:600;font-size:24px;color:var(--ink)}
.menu{position:absolute;right:24px;top:19px;display:flex;align-items:center;gap:44px;font-family:'Poppins',sans-serif;font-size:14px}
.btn{display:inline-block;background:var(--teal);color:var(--white);font-family:'Poppins',sans-serif;font-size:13px;border-radius:3px;padding:8px 15px}
.hero-h1{left:141px;top:196px;font-family:'Poppins',sans-serif;font-weight:400;font-size:48px;line-height:56px}
.hero-h1 b{font-weight:700;font-size:49px;display:block}
.hero-sub{left:141px;top:315px;font-family:'Poppins',sans-serif;font-size:14px}
.hero-btn{left:141px;top:353px;width:174px;height:33px;padding:8px 0;text-align:center}

/* section headers */
.sec-title{left:0;width:1200px;text-align:center;font-family:'Playfair Display',serif;font-weight:500;font-size:30px}
.sec-title span{border-bottom:3px solid var(--gold);padding-bottom:1px}
.sec-sub{left:0;width:1200px;text-align:center;font-size:12.5px;line-height:16px;color:var(--muted)}
.dark .sec-title,.dark .sec-sub{color:var(--white)}

.services-bg{left:0;top:627px;width:1200px;height:622px;background:var(--light)}
.svc{width:292px;height:187px;background:var(--card-teal);border-radius:18px;padding:22px 21px}
.svc-icon{width:42px;height:42px;border-radius:6px;background:var(--teal-soft);display:flex;align-items:center;justify-content:center}
.svc h3{font-family:'Playfair Display',serif;font-weight:500;font-size:20px;margin-top:40px;color:#1f2d3a}
.svc p{font-size:12.5px;line-height:15.5px;color:#3b4754;margin-top:2px}

/* why */
.why-bg{left:0;top:1249px;width:1200px;height:694px;background:var(--navy)}
.why{left:141px;width:423px;height:98px;background:var(--white);border-radius:6px;display:flex;align-items:center;padding:0 16px}
.why-icon{width:70px;height:70px;border-radius:6px;background:#e6ecec;display:flex;align-items:center;justify-content:center;flex:none}
.why-txt{margin-left:24px}
.why-txt h3{font-family:'Playfair Display',serif;font-weight:500;font-size:20px;color:#1f2d3a}
.why-txt p{font-size:12px;line-height:15.5px;color:var(--muted);margin-top:3px}
.why-frame{left:609px;top:1425px;width:458px;height:447px;background:var(--teal-soft);border-top-left-radius:80px;border-bottom-right-radius:110px}
.why-photo{left:600px;top:1435px;width:458px;height:437px;border-top-left-radius:80px;border-bottom-right-radius:110px;background:linear-gradient(135deg,#cfd6dc,#e9ecef 50%,#b9c2ca)}

/* visit */
.map{left:141px;top:2130px;width:642px;height:461px;background:linear-gradient(135deg,#dcecf5,#ece8dc 45%,#a8d8f2)}
.info{left:758px;top:2199px;width:300px;height:324px;background:var(--navy);border-radius:10px;padding:28px 28px;color:var(--white)}
.info h4{font-family:'Playfair Display',serif;font-weight:500;font-size:19px;display:flex;align-items:center;gap:6px}
.info p{font-size:12px;line-height:15px;margin-top:6px}
.info .blk{margin-bottom:20px}
.call-btn{display:inline-block;background:var(--white);color:var(--ink);font-size:12px;border-radius:3px;padding:8px 20px;margin-top:4px}

/* reviews */
.rev-bg{left:0;top:2662px;width:1200px;height:510px;background:var(--navy)}
.rev{top:2835px;width:448px;height:190px;background:var(--white);border-radius:8px;padding:20px 21px}
.stars{display:flex;gap:4px}
.date{position:absolute;right:22px;top:24px;font-size:12.5px;color:#333}
.quote{font-size:12.5px;line-height:15.5px;margin-top:19px;color:#333}
.person{position:absolute;left:21px;bottom:22px;display:flex;align-items:center;gap:14px}
.avatar{width:55px;height:55px;border-radius:50%;background:linear-gradient(135deg,#c79a78,#4a3a33)}
.avatar.b{background:linear-gradient(135deg,#f0d27a,#d9a877)}
.person b{font-family:'Playfair Display',serif;font-weight:500;font-size:20px;display:block}
.person small{font-size:12px;color:var(--muted)}
.arrow{width:30px;height:30px;border:1.5px solid var(--white);border-radius:5px;display:flex;align-items:center;justify-content:center}
.arrow.fill{background:var(--white)}
.view{left:548px;top:3069px;width:104px;height:38px;background:var(--teal-soft);color:var(--white);font-size:13px;text-align:center;line-height:38px;border-radius:3px}

/* footer */
.foot{left:0;top:3172px;width:1200px;height:278px;background:var(--footer);color:var(--white)}
.foot-brand{position:absolute;left:0;width:1200px;top:62px;text-align:center;font-family:'Playfair Display',serif;font-weight:500;font-size:24px}
.foot-links{position:absolute;left:0;width:1200px;top:126px;display:flex;justify-content:center;gap:28px;font-family:'Playfair Display',serif;font-size:13px}
.foot-social{position:absolute;left:0;width:1200px;top:164px;display:flex;justify-content:center;gap:30px}
.foot-social i{width:14px;height:14px;background:var(--white);border-radius:3px;display:block}
.foot-line{position:absolute;left:0;top:236px;width:1200px;height:1px;background:#3a3a3a}
.copy{position:absolute;left:0;width:1200px;top:250px;text-align:center;font-size:11px}
</style>
</head>
<body>

<div class="abs hero-photo" role="img" aria-label="Smiling young man in a denim shirt against a bright blue backdrop"></div>
<header class="abs nav">
  <div class="brand">Harrowfield Dentistry</div>
  <nav class="menu"><span>Home</span><span>About</span><span>Services</span><span>Contact</span><span class="btn" style="margin-left:-20px">Book an Appointment</span></nav>
</header>
<h1 class="abs hero-h1">Smile Confidently.<b>Feel the Difference.</b></h1>
<p class="abs hero-sub">Premium Dental Care Tailored to You – Where Comfort Meets Excellence</p>
<span class="abs btn hero-btn">Book an Appointment</span>

<div class="abs services-bg"></div>
<h2 class="abs sec-title" style="top:664px">Our Dental <span>Services</span></h2>
<p class="abs sec-sub" style="top:708px">Comprehensive, high-quality care from cosmetic enhancements to<br>emergency treatments—tailored to your smile.</p>

<div class="abs svc" style="left:141px;top:781px">
  <div class="svc-icon"><svg width="26" height="26" viewBox="0 0 26 26" fill="none" stroke="#fff" stroke-width="1.6"><circle cx="13" cy="13" r="10"/><path d="M8.5 15c2.5 3 6.5 3 9 0"/><circle cx="9.5" cy="10.5" r=".8" fill="#fff"/><circle cx="16.5" cy="10.5" r=".8" fill="#fff"/></svg></div>
  <h3>Cosmetic Dentistry</h3><p>Enhance your smile with treatments that improve tooth shape, color, and appearance.</p>
</div>
<div class="abs svc" style="left:455px;top:781px">
  <div class="svc-icon"><svg width="26" height="26" viewBox="0 0 26 26" fill="none" stroke="#fff" stroke-width="1.6"><path d="M7 6c2-2 4-1 6 0 2-1 4-2 6 0 1 3-1 6-2 7v7h-8v-7C8 12 6 9 7 6z"/><path d="M10 16h6M10 19h6"/></svg></div>
  <h3>Dental Implants</h3><p>Permanent, natural-looking tooth replacements that restore function and confidence.</p>
</div>
<div class="abs svc" style="left:767px;top:781px">
  <div class="svc-icon"><svg width="26" height="26" viewBox="0 0 26 26" fill="none" stroke="#fff" stroke-width="1.6"><path d="M6 6l14 14M20 6L6 20"/><circle cx="6" cy="6" r="2"/><circle cx="20" cy="6" r="2"/></svg></div>
  <h3>Emergency Services</h3><p>Quick, professional treatment for dental emergencies, providing relief when you need it most.</p>
</div>
<div class="abs svc" style="left:141px;top:991px">
  <div class="svc-icon"><svg width="26" height="26" viewBox="0 0 26 26" fill="none" stroke="#fff" stroke-width="1.6"><path d="M4 10h18c0 6-4 9-9 9s-9-3-9-9z"/><path d="M7 13h12M9 10v4M13 10v5M17 10v4"/></svg></div>
  <h3>Teeth Whitening</h3><p>Brighten your smile with safe, professional whitening treatments that deliver fast, noticeable results.</p>
</div>
<div class="abs svc" style="left:455px;top:991px">
  <div class="svc-icon"><svg width="26" height="26" viewBox="0 0 26 26" fill="none" stroke="#fff" stroke-width="1.6"><path d="M6 7c2-3 5-2 7-1 2-1 5-2 7 1 1 4-1 7-2 9l-1 5h-2l-2-5-2 5H9l-1-5C7 14 5 11 6 7z"/><path d="M20 3v3M18.5 4.5h3"/></svg></div>
  <h3>Dental Hygiene</h3><p>Preventive cleanings and exams to keep your teeth and gums healthy, fresh, and cavity-free.</p>
</div>
<div class="abs svc" style="left:767px;top:991px">
  <div class="svc-icon"><svg width="26" height="26" viewBox="0 0 26 26" fill="none" stroke="#fff" stroke-width="1.6"><path d="M6 7c2-3 5-2 7-1 2-1 5-2 7 1 1 4-1 7-2 9l-1 5h-2l-2-5-2 5H9l-1-5C7 14 5 11 6 7z"/><path d="M10 9l2 3"/></svg></div>
  <h3>Tooth Restoration</h3><p>Repair and restore teeth with fillings, crowns, bridges, and custom dentures for a healthier smile.</p>
</div>

<div class="abs why-bg"></div>
<div class="dark">
  <h2 class="abs sec-title" style="top:1305px">Why <span>Choose</span> Us?</h2>
  <p class="abs sec-sub" style="top:1349px">Experience expert care in a modern, comfort-first clinic—where<br>advanced technology meets personalized treatment.</p>
</div>

<div class="abs why" style="top:1435px">
  <div class="why-icon"><svg width="34" height="34" viewBox="0 0 34 34" fill="none" stroke="#4fb8ab" stroke-width="2"><rect x="3" y="7" width="28" height="20" rx="2"/><rect x="8" y="11" width="18" height="12" rx="1"/><path d="M13 14c1-1 3-1 4 0 1-1 3-1 4 0 0 3-1 4-1 5h-6c0-1-1-2-1-5z"/></svg></div>
  <div class="why-txt"><h3>Board-Certified Dentists</h3><p>Expertise you can trust, backed by advanced training<br>and credentials.</p></div>
</div>
<div class="abs why" style="top:1549px">
  <div class="why-icon"><svg width="34" height="34" viewBox="0 0 34 34" fill="#4fb8ab"><path d="M9 8c3-4 6-2 8-1 2-1 5-3 8 1 2 5-1 9-2 11l-1 10h-3l-2-8-2 8h-3l-1-10C9 17 7 13 9 8z"/></svg></div>
  <div class="why-txt"><h3>Pain-Free Treatments</h3><p>Gentle techniques and modern technology for a stress-<br>free experience.</p></div>
</div>
<div class="abs why" style="top:1662px">
  <div class="why-icon"><svg width="34" height="34" viewBox="0 0 34 34" fill="none" stroke="#4fb8ab" stroke-width="2"><path d="M6 8l6 12h14M12 20l-3 8M20 20v8M16 28h8"/><circle cx="24" cy="9" r="3"/></svg></div>
  <div class="why-txt"><h3>Luxury, Comfort-First Clinic</h3><p>Designed to help you relax—because your comfort<br>matters.</p></div>
</div>
<div class="abs why" style="top:1774px">
  <div class="why-icon"><svg width="34" height="34" viewBox="0 0 34 34" fill="#4fb8ab"><rect x="5" y="11" width="24" height="17" rx="3"/><path d="M8 11l14-6 3 6z"/><circle cx="24" cy="19.5" r="2" fill="#e6ecec"/></svg></div>
  <div class="why-txt"><h3>Flexible Payment Plans</h3><p>Quality care made accessible with tailored financing<br>options.</p></div>
</div>

<div class="abs why-frame"></div>
<div class="abs why-photo" role="img" aria-label="Smiling female dentist in a white coat with arms crossed in a bright clinic"></div>

<h2 class="abs sec-title" style="top:2013px">Visit Our <span>Clinic</span></h2>
<p class="abs sec-sub" style="top:2058px">Located in the heart of Harrowfield, our clinic offers flexible hours and easy<br>access to premium dental care.</p>
<div class="abs map" role="img" aria-label="Street map showing the clinic location in the city"></div>
<div class="abs info">
  <div class="blk"><h4><svg width="16" height="16" viewBox="0 0 16 16" fill="none" stroke="#5fbfb2" stroke-width="1.4"><path d="M8 15s5-5 5-9A5 5 0 0 0 3 6c0 4 5 9 5 9z"/><circle cx="8" cy="6" r="1.8"/></svg>Visit Us</h4><p style="margin-left:10px">48 Willow Crest Ave, Harrowfield</p></div>
  <div class="blk"><h4><svg width="16" height="16" viewBox="0 0 16 16" fill="none" stroke="#5fbfb2" stroke-width="1.4"><circle cx="8" cy="8" r="6.5"/><path d="M8 4v4l3 2"/></svg>Operating Hours</h4><p>Mon–Fri: 8:00 AM – 6:00 PM<br>Sat: 9:00 AM – 2:00 PM<br>Closed Sundays</p></div>
  <div class="blk"><h4><svg width="16" height="16" viewBox="0 0 16 16" fill="none" stroke="#5fbfb2" stroke-width="1.4"><path d="M3 2h3l1.5 3.5-2 1.2a8 8 0 0 0 3.8 3.8l1.2-2L14 10v3a1 1 0 0 1-1 1A11 11 0 0 1 2 3a1 1 0 0 1 1-1z"/></svg>Call Us</h4><p>(555) 214-3380</p><span class="call-btn">Call Now</span></div>
</div>

<div class="abs rev-bg"></div>
<div class="dark">
  <h2 class="abs sec-title" style="top:2717px">What Our <span>Patients Say</span></h2>
  <p class="abs sec-sub" style="top:2762px">Real stories from patients who've experienced compassionate care,<br>outstanding results, and a confident new smile.</p>
</div>

<div class="abs arrow" style="left:91px;top:2919px"><svg width="12" height="12" viewBox="0 0 12 12" fill="none" stroke="#fff" stroke-width="1.6"><path d="M8 1L3 6l5 5"/></svg></div>
<div class="abs arrow fill" style="left:1080px;top:2919px"><svg width="12" height="12" viewBox="0 0 12 12" fill="none" stroke="#2d3e50" stroke-width="1.6"><path d="M4 1l5 5-5 5"/></svg></div>

<div class="abs rev" style="left:141px">
  <div class="stars">
    <svg width="22" height="21" viewBox="0 0 22 21"><path fill="#e2b53c" d="M11 0l3.2 6.9 7.5.8-5.6 5.1 1.6 7.4L11 16.4 4.3 20.2l1.6-7.4L.3 7.7l7.5-.8z"/></svg>
    <svg width="22" height="21" viewBox="0 0 22 21"><path fill="#e2b53c" d="M11 0l3.2 6.9 7.5.8-5.6 5.1 1.6 7.4L11 16.4 4.3 20.2l1.6-7.4L.3 7.7l7.5-.8z"/></svg>
    <svg width="22" height="21" viewBox="0 0 22 21"><path fill="#e2b53c" d="M11 0l3.2 6.9 7.5.8-5.6 5.1 1.6 7.4L11 16.4 4.3 20.2l1.6-7.4L.3 7.7l7.5-.8z"/></svg>
    <svg width="22" height="21" viewBox="0 0 22 21"><path fill="#e2b53c" d="M11 0l3.2 6.9 7.5.8-5.6 5.1 1.6 7.4L11 16.4 4.3 20.2l1.6-7.4L.3 7.7l7.5-.8z"/></svg>
    <svg width="22" height="21" viewBox="0 0 22 21"><path fill="#e2b53c" d="M11 0l3.2 6.9 7.5.8-5.6 5.1 1.6 7.4L11 16.4 4.3 20.2l1.6-7.4L.3 7.7l7.5-.8z"/></svg>
  </div>
  <span class="date">10th Feb, 2023</span>
  <p class="quote">"The team made me feel comfortable from the moment I walked in. My<br>smile has never looked better!"</p>
  <div class="person"><div class="avatar" role="img" aria-label="Patient portrait"></div><div><b>Daniel R.</b><small>Customer</small></div></div>
</div>
<div class="abs rev" style="left:611px">
  <div class="stars">
    <svg width="22" height="21" viewBox="0 0 22 21"><path fill="#e2b53c" d="M11 0l3.2 6.9 7.5.8-5.6 5.1 1.6 7.4L11 16.4 4.3 20.2l1.6-7.4L.3 7.7l7.5-.8z"/></svg>
    <svg width="22" height="21" viewBox="0 0 22 21"><path fill="#e2b53c" d="M11 0l3.2 6.9 7.5.8-5.6 5.1 1.6 7.4L11 16.4 4.3 20.2l1.6-7.4L.3 7.7l7.5-.8z"/></svg>
    <svg width="22" height="21" viewBox="0 0 22 21"><path fill="#e2b53c" d="M11 0l3.2 6.9 7.5.8-5.6 5.1 1.6 7.4L11 16.4 4.3 20.2l1.6-7.4L.3 7.7l7.5-.8z"/></svg>
    <svg width="22" height="21" viewBox="0 0 22 21"><path fill="#e2b53c" d="M11 0l3.2 6.9 7.5.8-5.6 5.1 1.6 7.4L11 16.4 4.3 20.2l1.6-7.4L.3 7.7l7.5-.8z"/></svg>
    <svg width="22" height="21" viewBox="0 0 22 21"><path fill="#e2b53c" d="M11 0l3.2 6.9 7.5.8-5.6 5.1 1.6 7.4L11 16.4 4.3 20.2l1.6-7.4L.3 7.7l7.5-.8z"/></svg>
  </div>
  <span class="date">06th Feb, 2023</span>
  <p class="quote">"Beautiful clinic, friendly staff, and pain-free treatment. Truly a premium<br>dental experience."</p>
  <div class="person"><div class="avatar b" role="img" aria-label="Patient portrait"></div><div><b>Clara W.</b><small>Customer</small></div></div>
</div>
<div class="abs view">View All</div>

<footer class="abs foot">
  <div class="foot-brand">Harrowfield Dentistry</div>
  <nav class="foot-links"><span>Home</span><span>Our Services</span><span>Contact Us</span></nav>
  <div class="foot-social"><i></i><i></i><i></i></div>
  <div class="foot-line"></div>
  <p class="copy">© 2025 Harrowfield Dentistry. All Rights Reserved.</p>
</footer>

</body>
</html>
```